Post Card Design

I need a post card design for an Educational Program - targeted at professionals and people interested in self development and awareness. The PDF file attached is an example of the program being offered at another company "The Brightwater Studio" The Tree Logo and The Brightwater Studio can NOT be used as this program maybe offered at places other than The Brightwater Studio . A blank spot should be left where I will use a separate sticker to indicate the time and location of the next course. The MAIN Title text will be "STRENGTH AND COURAGE" instead of "Harmony Growth Workshop "HGW"
I am attaching my own logo. The image of the Sun and the Pathway should be used. DO NOT use the Logo text "SerenityMeadows or name and tagline. The image of the Sun and the pathway could be used as a watermark background filling the whole of one side of the card. I am attaching an image of me that should go in a small place. I will need to edit text and content myself after I choose the design. I would like one with rounded corners

```html
<!DOCTYPE html>
<html lang="en">
<head>
<meta charset="utf-8">
<title>Strength and Courage Program – Postcard</title>
<link rel="stylesheet" href="https://fonts.googleapis.com/css2?family=Source+Sans+3:wght@400;600;700&display=swap">
<style>
  :root {
    --frame-blue: #2fa8dc;
    --band-green: #d4e39d;
    --box-green: #b1cf3b;
    --ink: #111111;
    --page: #ffffff;
    --photo-tone: #5b6b73;
    --watermark-sun: #fbe7b2;
    --watermark-hill: #e4edc4;
  }
  * { margin: 0; padding: 0; box-sizing: border-box; }
  html, body {
    width: 1200px; height: 929px; overflow: hidden;
    background: var(--page);
  }
  body {
    position: relative;
    font-family: "Source Sans 3", "Myriad Pro", sans-serif;
    color: var(--ink);
  }
  .postcard {
    position: absolute; left: 35px; top: 35px;
    width: 1127px; height: 858px;
    border: 9px solid var(--frame-blue);
    border-radius: 46px;
    overflow: hidden;
    background: var(--page);
  }
  .watermark {
    position: absolute; left: 120px; top: 380px;
    width: 1000px; height: 470px;
  }
  .instructor-band {
    position: absolute; left: 0; top: 0;
    width: 100%; height: 338px;
    background: var(--band-green);
  }
  .instructor-photo {
    position: absolute; left: 29px; top: 27px;
    width: 191px; height: 269px;
  }
  .instructor-bio {
    position: absolute; left: 246px; top: 34px; width: 838px;
  }
  .instructor-bio h2 {
    font-size: 27px; font-weight: 700; margin-bottom: 8px;
  }
  .instructor-bio p {
    font-size: 22px; line-height: 29.6px; text-align: justify;
    margin-bottom: 11px;
  }
  .instructor-bio strong { font-weight: 700; }
  .cost-box {
    position: absolute; left: 29px; top: 374px;
    width: 514px; height: 229px;
    background: var(--box-green);
    border-radius: 11px;
    text-align: center;
    padding-top: 22px;
  }
  .cost-box h3 { font-size: 28px; font-weight: 700; line-height: 36px; }
  .cost-box .price { font-size: 27px; line-height: 46px; }
  .cost-box .note { font-size: 21px; line-height: 34px; }
  .cost-box .contact-note { font-size: 21px; line-height: 36px; margin-top: 3px; }
  .schedule {
    position: absolute; left: 47px; top: 645px;
  }
  .schedule h3 { font-size: 27px; font-weight: 700; line-height: 36px; }
  .schedule .dates { font-size: 23px; line-height: 36px; }
  .schedule .holiday { font-size: 20.5px; line-height: 36px; }
  .registration {
    position: absolute; right: 44px; top: 392px;
    text-align: right; font-size: 23px; line-height: 32px;
  }
  .registration h3 { font-size: 24px; font-weight: 700; line-height: 34px; }
  .registration .more-info { margin-top: 34px; }
  .registration .phone { font-weight: 700; }
  .registration .website { margin-top: 36px; }
</style>
</head>
<body>
  <div class="postcard">
    <svg class="watermark" role="img" aria-label="Faint sun and pathway background watermark area" viewBox="0 0 1000 470">
      <defs>
        <radialGradient id="wm-glow" cx="0.42" cy="0.55" r="0.6">
          <stop offset="0" stop-color="var(--watermark-sun)" stop-opacity="0.85"/>
          <stop offset="0.7" stop-color="var(--watermark-hill)" stop-opacity="0.45"/>
          <stop offset="1" stop-color="var(--page)" stop-opacity="0"/>
        </radialGradient>
      </defs>
      <rect width="1000" height="470" fill="url(#wm-glow)"/>
    </svg>

    <section class="instructor-band">
      <svg class="instructor-photo" role="img" aria-label="Portrait photo of the program instructor" viewBox="0 0 191 269">
        <defs>
          <linearGradient id="photo-tone" x1="0" y1="0" x2="0" y2="1">
            <stop offset="0" stop-color="#8a9aa2"/>
            <stop offset="1" stop-color="var(--photo-tone)"/>
          </linearGradient>
        </defs>
        <rect width="191" height="269" rx="6" fill="url(#photo-tone)"/>
      </svg>
      <div class="instructor-bio">
        <h2>Strength and Courage&nbsp; Program Instructor</h2>
        <p><strong>Marisol Venn</strong> has been working as a psychotherapist for 10 years. She has specialized training in Cognitive Behavioural Therapy (CBT), mindfulness, and compassion. Her training in mind-body approaches helps people to have greater ease and confidence when faced with anxiety and stress.</p>
        <p>Marisol has a special interest in teaching self-compassion and has completed teacher training in Harmony Growth through Westbrook University. Marisol has an M.Ed. from the Northgate University and is a psychotherapist, workshop facilitator, and certified yoga instructor at The Brightwater Studio.</p>
      </div>
    </section>

    <section class="cost-box">
      <h3>Cost &amp; Requirements for Program</h3>
      <p class="price">$100 per week, for 8 weeks</p>
      <p class="note">(After initial $175 deposit; covered by most<br>extended insurance plans.)</p>
      <p class="contact-note">Please contact us to discuss payment options.</p>
    </section>

    <section class="schedule">
      <h3>SCHEDULE</h3>
      <p class="dates">Mondays, March 24 – May 26, 2014<br>from 6:00 – 8:00 p.m.</p>
      <p class="holiday">Please note that the group will not meet on<br>April 21st or May 19th due to holidays.</p>
    </section>

    <section class="registration">
      <h3>Location &amp; Registration</h3>
      <p>Name of Organisation<br>Address Address<br>Address Address<br>Address Address</p>
      <p class="more-info">For more information<br>or to schedule a free consultation,<br>contact us at<br><span class="phone">000-000-0000</span><br>or email id</p>
      <p class="website">website address</p>
    </section>
  </div>
</body>
</html>
```